Quillmere Supply Chain and Logistic Consulting

Please review the attached Business Card. I want as close to this card with the colors, fonts, and quality of the card as possible. The attached compass should replace the deer head on both sides of the card and the text should say:

Backside
Compass JPEG
Quillmere SC&L
A Supply Chain and Logistics Consulting Company

Frontside
Quillmere SC&L
Ray Falkner - Brinlow Coast
President
____________________________________
(555) 314-9027
QuillmereSCL@Examplemail.com
_____________________________________

Bottom Front Side

Target Market(s)

Businesses

Contact Information for Business Card

Backside
Compass JPEG
Quillmere SC&L

Frontside
Quillmere SC&L
President
(555) 314-9027
QuillmereSCL@Examplemail.com

Bottom Front Side

Font styles to use
Serif
Script

Colors

Designer to choose colors to be used in the design.

Requirements
Must have
• See attached card for reference
Nice to have
Should not have

```html
<!DOCTYPE html>
<html lang="en">
<head>
<meta charset="utf-8">
<title>Quillmere SC&amp;L – Business Card</title>
<link rel="stylesheet" href="https://fonts.googleapis.com/css2?family=Cinzel:wght@400&family=Tinos:wght@400;700&display=swap">
<style>
  :root {
    --backdrop: #3b3b3d;
    --card-white: #ffffff;
    --navy: #13285a;
    --ink: #2e2e2e;
    --rule: #c9c9c9;
    --blue-light: #a9bdd7;
    --blue-mid: #4f6c97;
    --blue-deep: #0c1f45;
    --white: #ffffff;
  }
  * { margin: 0; padding: 0; box-sizing: border-box; }
  html, body { width: 1200px; height: 1200px; overflow: hidden; }
  body { background: var(--backdrop); position: relative; }

  .card {
    position: absolute;
    top: 310px;
    width: 364px;
    height: 594px;
    text-align: center;
  }
  .card--front { left: 234px; background: var(--card-white); }
  .card--back { left: 628px; width: 369px; background: var(--blue-deep); overflow: hidden; }

  .compass-area {
    position: absolute;
    left: 97px;
    top: 72px;
    width: 170px;
    height: 170px;
    border-radius: 50%;
    background: radial-gradient(circle at 50% 50%, var(--blue-light) 0%, var(--blue-mid) 60%, var(--navy) 100%);
  }
  .backdrop-art {
    position: absolute;
    inset: 0;
    background: radial-gradient(ellipse 75% 60% at 48% 48%, var(--blue-light) 0%, var(--blue-mid) 55%, var(--blue-deep) 100%);
  }

  .wordmark {
    position: absolute;
    left: 0; right: 0;
    font-family: "Tinos", serif;
    font-weight: 400;
    line-height: 1;
  }
  .card--front .wordmark { top: 284px; font-size: 32px; color: var(--navy); }
  .card--back .wordmark { top: 440px; font-size: 40px; color: var(--white); }

  .person { position: absolute; left: 0; right: 0; top: 374px; font-family: "Tinos", serif; }
  .person__name { font-size: 21px; font-weight: 700; color: var(--navy); line-height: 24px; }
  .person__title { font-size: 16px; color: var(--ink); line-height: 20px; }

  .rule { position: absolute; left: 30px; right: 30px; height: 1px; background: var(--rule); }
  .rule--top { top: 428px; }
  .rule--bottom { top: 493px; }

  .contact {
    position: absolute; left: 0; right: 0; top: 437px;
    font-family: "Tinos", serif; font-size: 16px; color: var(--ink); line-height: 22px;
  }

  .tagline {
    position: absolute; left: 0; right: 0;
    font-family: "Cinzel", serif;
    font-size: 19px;
    line-height: 22px;
  }
  .card--front .tagline { top: 508px; color: var(--navy); }
  .card--back .tagline { top: 502px; color: var(--white); }
</style>
</head>
<body>
  <section class="card card--front">
    <div class="compass-area" role="img" aria-label="Compass rose illustration"></div>
    <div class="wordmark">Quillmere SC&amp;L</div>
    <div class="person">
      <div class="person__name">Ray Falkner - Brinlow Coast</div>
      <div class="person__title">President</div>
    </div>
    <div class="rule rule--top"></div>
    <div class="contact">
      <div>(555) 314-9027</div>
      <div>QuillmereSCL@Examplemail.com</div>
    </div>
    <div class="rule rule--bottom"></div>
    <div class="tagline">A Supply Chain and Logistics<br>Consulting Company</div>
  </section>

  <section class="card card--back">
    <div class="backdrop-art" role="img" aria-label="Large faded compass rose illustration in blue tones"></div>
    <div class="wordmark">Quillmere SC&amp;L</div>
    <div class="tagline">A Supply Chain and Logistics<br>Consulting Company</div>
  </section>
</body>
</html>
```